Store Front Signage for an Upscale Cake & Dessert Bakery

We need a design for store front windows. We are a 12 year old bakery specializing in cakes, cupcakes, cookies, pies, and other desserts. We recently moved to a high traffic location.. and we would like to boost our visual presence; we can be seen from the main road but are competing with other businesses for attention. Attached is a photo of our store front with posters but this signage will be for window film for the entire window span. (see the store front to the left of the photo to see the green and yellow as a film example)
Our logo and store sign (not like in photo, that is showing more red) are in shades of pink. The most visible part of the signage is in the upper third to upper half of the 60" panels.
The signs in the window currently say Life's Short. Eat Cake.
We now use Enjoy Life. Eat Cake.
The design should span all the windows and door -- this can be individual panels or one design that covers all panels. I have pink and greys chosen but please DO NOT let this constrain you. The inside of the bakery has grey floors and walls. white cabinetry, black granite countertops. The only thing with color is the baked goods and display cakes, pictures of cakes, the logo and menu and employee shirts.

Target Market(s)

we are located at a busy intersection --- we would like to capture the attention of people in cars as they pass by and entice them to stop in

Font styles to use
Serif
Sans Serif

Colors
d3d3d3
757575
ffffff
e24197
e667a6
eea4c8
f9d9e8

Requirements
Must have
• I would like the design to be easily discernible at the road way that is about 75 feet from store front. If you look at the photos I provide, note that the font size that is easily readable from the road are the ones in the top panes (although the shadow from the building makes them difficult to see -- the best visibility is the top 1/3 of the 60" panels.
Nice to have
• would like to have some non-photo graphics of a cake ( like a birthday cake), tiered cake, cupcakes, and cookies or pie for the panels --- but DO NOT let this constrain you. I need something to grab attention while cars are stopped at the nearby traffic light.
• If this design works well... I will be changing the panel on a seasonal basis
Should not have
• words that cannot be read from a distance.

```html
<!DOCTYPE html>
<html lang="en">
<head>
<meta charset="utf-8">
<title>Merrowby's Bake Shoppe – Window Film</title>
<link rel="stylesheet" href="https://fonts.googleapis.com/css2?family=Kreon:wght@300;400&family=Open+Sans:wght@400;700&display=swap">
<style>
  :root {
    --page: #ecebea;
    --frame: #0d0d0d;
    --panel: #161616;
    --plum: #8d1f62;
    --plum-deep: #7a1854;
    --plum-soft: #b0578b;
    --pink: #eea4c8;
    --pink-soft: #f9d9e8;
    --white: #ffffff;
  }
  * { box-sizing: border-box; margin: 0; padding: 0; }
  html, body { width: 1200px; height: 635px; overflow: hidden; background: var(--page); }

  .storefront {
    position: absolute; left: 20px; top: 20px;
    width: 1160px; height: 595px;
    background: var(--frame);
    padding: 8px;
    display: grid;
    grid-template-columns: 1fr 1fr 0.72fr 1fr 1fr;
    grid-template-rows: 138px 1fr 118px;
    gap: 8px;
  }

  /* awning area */
  .awning {
    background: linear-gradient(to bottom, var(--plum) 0%, var(--plum-soft) 60%, var(--pink-soft) 100%);
  }

  /* message panels */
  .pane {
    position: relative; overflow: hidden;
    display: flex; flex-direction: column; align-items: center; justify-content: center;
    text-align: center; color: var(--white);
  }
  .pane-texture { position: absolute; inset: 0; background: var(--panel); }
  .pane > *:not(.pane-texture) { position: relative; }

  .brand-name {
    font-family: "Kreon", serif; font-weight: 400;
    color: var(--pink); letter-spacing: .06em; text-transform: uppercase;
    display: flex; align-items: center; gap: 8px;
  }
  .brand-name .dot { width: 12px; height: 12px; border-radius: 50%; background: var(--pink); }
  .brand-name.large { font-size: 24px; margin-bottom: 10px; }
  .brand-name.small { font-size: 14px; margin-bottom: 4px; }
  .brand-name.small .dot { width: 8px; height: 8px; }

  .shop-type { font-family: "Kreon", serif; font-weight: 300; line-height: .95; }
  .shop-type.large { font-size: 46px; }
  .shop-type.small { font-size: 26px; }

  .rule { width: 96px; height: 2px; background: var(--pink); margin-top: 16px; position: relative; }
  .rule::after {
    content: ""; position: absolute; left: 50%; top: 50%;
    width: 8px; height: 8px; border-radius: 50%; background: var(--pink);
    transform: translate(-50%, -50%);
  }
  .rule.small { width: 70px; height: 1px; margin: 10px 0 14px; }
  .rule.small::after { width: 5px; height: 5px; }

  .offer { font-family: "Kreon", serif; font-weight: 300; font-size: 24px; line-height: 1; }
  .bullet { width: 20px; height: 20px; border-radius: 50%; background: var(--pink); margin: 14px 0; }
  .note {
    font-family: "Open Sans", sans-serif; font-size: 13px; line-height: 1.2;
    text-transform: uppercase; margin-top: 6px;
  }
  .hours {
    font-family: "Open Sans", sans-serif; font-weight: 700; font-size: 10px;
    line-height: 1.3; text-transform: uppercase;
  }

  /* base band */
  .base { background: var(--plum); border-top: 6px solid var(--plum-deep); }
  .base.door-base { margin-bottom: 22px; }
</style>
</head>
<body>
  <main class="storefront">
    <div class="awning" role="img" aria-label="Striped plum and white scalloped awning illustration"></div>
    <div class="awning" role="img" aria-label="Striped plum and white scalloped awning illustration"></div>
    <div class="awning" role="img" aria-label="Striped plum and white scalloped awning illustration"></div>
    <div class="awning" role="img" aria-label="Striped plum and white scalloped awning illustration"></div>
    <div class="awning" role="img" aria-label="Striped plum and white scalloped awning illustration"></div>

    <section class="pane brand-pane">
      <div class="pane-texture" role="img" aria-label="Black background with subtle grey damask scroll pattern"></div>
      <p class="brand-name large"><span class="dot"></span>Merrowby's</p>
      <p class="shop-type large">bake<br>shoppe</p>
      <div class="rule"></div>
    </section>

    <section class="pane offer-pane">
      <div class="pane-texture" role="img" aria-label="Black background with subtle grey damask scroll pattern"></div>
      <p class="offer">custom<br>cakes</p>
      <div class="bullet"></div>
      <p class="offer">holiday<br>desserts</p>
      <div class="bullet"></div>
      <p class="note">Order online<br>merrowbys.com</p>
    </section>

    <section class="pane door-pane">
      <div class="pane-texture" role="img" aria-label="Black background with subtle grey damask scroll pattern"></div>
      <p class="brand-name small"><span class="dot"></span>Merrowby's</p>
      <p class="shop-type small">bake<br>shoppe</p>
      <div class="rule small"></div>
      <p class="hours">Hours:<br>Monday-Saturday<br>9am – 7pm<br>Sunday 11am-5pm</p>
    </section>

    <section class="pane offer-pane">
      <div class="pane-texture" role="img" aria-label="Black background with subtle grey damask scroll pattern"></div>
      <p class="offer">cupcakes<br>galore</p>
      <div class="bullet"></div>
      <p class="offer">sweets and<br>cookies</p>
      <div class="bullet"></div>
      <p class="note">Next day pick-up<br>delivery available</p>
    </section>

    <section class="pane brand-pane">
      <div class="pane-texture" role="img" aria-label="Black background with subtle grey damask scroll pattern"></div>
      <p class="brand-name large"><span class="dot"></span>Merrowby's</p>
      <p class="shop-type large">bake<br>shoppe</p>
      <div class="rule"></div>
    </section>

    <div class="base" role="img" aria-label="Plum band with pink lace border and scroll ornament pattern"></div>
    <div class="base" role="img" aria-label="Plum band with pink lace border and scroll ornament pattern"></div>
    <div class="base door-base" role="img" aria-label="Plum band with pink lace border and scroll ornament pattern"></div>
    <div class="base" role="img" aria-label="Plum band with pink lace border and scroll ornament pattern"></div>
    <div class="base" role="img" aria-label="Plum band with pink lace border and scroll ornament pattern"></div>
  </main>
</body>
</html>
```